Dynamic Business Card for Sports Supplements Company

Hi! I'm looking for an awesome business card to match my existing sports supplement company. I have uploaded my current company logo and screenshot of the front page of my website.

I would like to have something dynamic and interesting and utilize the colors in the website - the reds and purples

The business card should be double sided and focus on a unique eye-catching design on the back and include all the relevant company info.

Most importantly, it should say somewhere: "Sign up on our website for a coupon code."

Target Market(s)

Mostly for women gym goers but it shouldn't be too feminine. It should be in keeping with the website design. It should flow and clearly be connected to it

Industry/Entity Type

Business

Contact Information for Business Card

Lorraine K. Vestal
CEO
LVestal@Quorvanexco.com
www.quorvanexco.com
555.417.3820
P.O. Box 47315
Harlow Creek, Westmere 00000

Sign up on our website for a coupon code

Font styles to use
Serif
Sans Serif
Other font styles liked:
• Novecento font family and "Quorvanex" is in AR Destine font

Requirements
Must have
• One side should be a bold Quorvanex logo design. Even just the symbol itself may be o.k. (see attached file)

```html
<!DOCTYPE html>
<html lang="en">
<head>
<meta charset="utf-8">
<title>Quorvanex Business Card</title>
<link href="https://fonts.googleapis.com/css2?family=Source+Sans+3:ital,wght@0,400;0,600;0,700;1,400&display=swap" rel="stylesheet">
<style>
  :root {
    --backdrop: #5b4b3e;
    --brand-red: #ed1c24;
    --brand-black: #000000;
    --white: #ffffff;
    --card-w: 615px;
    --card-h: 352px;
  }
  html, body {
    margin: 0;
    padding: 0;
    width: 1200px;
    height: 987px;
    overflow: hidden;
    background: var(--backdrop);
    font-family: "Source Sans 3", "Myriad Pro", Arial, sans-serif;
  }
  .card {
    position: absolute;
    left: 293px;
    width: var(--card-w);
    height: var(--card-h);
    background: var(--brand-red);
    overflow: hidden;
    box-shadow: 0 3px 6px rgba(0,0,0,0.35);
    color: var(--white);
  }
  .card--front { top: 130px; }
  .card--back { top: 506px; }

  .front-bands {
    position: absolute;
    inset: 0;
    width: 100%;
    height: 100%;
  }
  .brand-name {
    position: absolute;
    left: 0;
    right: 0;
    text-align: center;
    font-weight: 700;
    color: var(--white);
    margin: 0;
    line-height: 1;
  }
  .card--front .brand-name {
    top: 128px;
    font-size: 30px;
    letter-spacing: 1px;
  }
  .holder {
    position: absolute;
    left: 28px;
    top: 238px;
    font-size: 17px;
    line-height: 22.5px;
  }
  .holder-name {
    font-weight: 600;
    font-size: 21px;
    line-height: 24px;
    display: block;
  }
  .contact {
    position: absolute;
    right: 18px;
    top: 261px;
    list-style: none;
    margin: 0;
    padding: 0;
    font-size: 17px;
    line-height: 23px;
    text-align: right;
  }
  .contact li {
    display: flex;
    justify-content: flex-end;
    align-items: center;
    gap: 6px;
  }
  .contact svg { width: 15px; height: 15px; flex: none; }

  .card--back .brand-name {
    top: 134px;
    font-size: 64px;
    letter-spacing: 2px;
  }
  .coupon-note {
    position: absolute;
    left: 0;
    right: 0;
    top: 289px;
    margin: 0;
    text-align: center;
    font-style: italic;
    font-size: 16.5px;
  }
</style>
</head>
<body>

<section class="card card--front" aria-label="Card front">
  <svg class="front-bands" viewBox="0 0 525 300" preserveAspectRatio="none" aria-hidden="true">
    <polygon points="0,0 525,0 525,114 263,229 0,114" fill="var(--brand-black)"/>
    <polyline points="0,103 263,218 525,103" fill="none" stroke="var(--brand-red)" stroke-width="4.5"/>
    <polyline points="0,110.5 263,225.5 525,110.5" fill="none" stroke="var(--white)" stroke-width="3"/>
  </svg>

  <p class="brand-name">QUORVANEX</p>

  <div class="holder">
    <span class="holder-name">Lorraine K. Vestal</span>
    CEO<br>
    P.O. Box 47315<br>
    Harlow Creek, Westmere 00000
  </div>

  <ul class="contact">
    <li>555.417.3820
      <svg viewBox="0 0 16 16" aria-hidden="true"><path fill="#fff" d="M3.6 1.2l2.2 2.6c.4.4.3 1-.1 1.4l-1 1c.9 2 2.4 3.5 4.4 4.4l1-1c.4-.4 1-.5 1.4-.1l2.6 2.2c.4.4.4 1 0 1.4l-1.3 1.3C10.4 16 1 6.6 2.6 4.3L3.9 3c.1-.1.1-.1-.3-1.8z"/></svg>
    </li>
    <li>LVestal@Quorvanexco.com
      <svg viewBox="0 0 16 16" aria-hidden="true"><rect x="1" y="3" width="14" height="10" fill="#fff"/><polyline points="1,3 8,9 15,3" fill="none" stroke="var(--brand-red)" stroke-width="1.3"/></svg>
    </li>
    <li>www.quorvanexco.com
      <svg viewBox="0 0 16 16" aria-hidden="true"><circle cx="8" cy="8" r="7" fill="#fff"/><path fill="var(--brand-red)" d="M5 4c1 0 2 1 1.5 2S4 7 5 8.5 7 10 6.5 12 5 12 4.5 11 3 8 3.5 6 4 4 5 4zM10 3.5c1 .5 2.5 1.5 2.5 3s-1.5 1-2 0-1.5-1-1-2 0-1 .5-1z"/></svg>
    </li>
  </ul>
</section>

<section class="card card--back" aria-label="Card back">
  <p class="brand-name">QUORVANEX</p>
  <p class="coupon-note">Sign up on our website for a coupon code</p>
</section>

</body>
</html>
```